Business Card Design Project

Company Name - Solvane Care

Wellness consulting and training company. Run through a medical centre.

Main colour themes are orange and blue, as in the logo. Want to replicate same effect with business cards.

To give a sense of freedom and potential as per the company name.

Want the business card to be in line with stationary design, which I have launched as well.

Double sided with design and colour on one side and details on other side.

Reason: Need business card and stationary design to be teed up.

Target Market(s)

35 to 65 age group.
New age and trendy

Industry/Entity Type

Training

Requirements
Must have
• Colours orange and blue as per logo
Nice to have
• Design to be similar to stationary design, letterhead and envelopes

```html
<!DOCTYPE html>
<html lang="en">
<head>
<meta charset="utf-8">
<title>Solvane Care – Stationery Set</title>
<link href="https://fonts.googleapis.com/css2?family=Arimo:wght@400;700&family=Pathway+Gothic+One&family=Mrs+Saint+Delafield&display=swap" rel="stylesheet">
<style>
:root{
  --blue:#0a4fa3;
  --blue-deep:#063f8a;
  --blue-light:#2f74c4;
  --orange:#f26a21;
  --ink:#1c1c1c;
  --paper:#ffffff;
  --backdrop:#3a3a3b;
}
*{margin:0;padding:0;box-sizing:border-box}
html,body{width:1200px;height:726px;overflow:hidden}
body{
  background:radial-gradient(ellipse at 50% 40%,#434344,var(--backdrop) 70%,#2c2c2d);
  font-family:"Arimo",Arial,sans-serif;color:var(--ink);position:relative;
}
.sheet{position:absolute;background:var(--paper);overflow:hidden;box-shadow:0 2px 6px rgba(0,0,0,.55)}
.wordmark{font-family:"Pathway Gothic One","Arial Narrow",sans-serif;color:var(--blue);white-space:nowrap;line-height:1}
.wave{position:absolute;left:0;bottom:0;display:block}

/* letterhead */
.letterhead{left:36px;top:19px;width:527px;height:682px}
.letterhead .wordmark{position:absolute;left:50px;top:62px;font-size:29px}
.contact{position:absolute;right:50px;top:71px;text-align:right;font-size:8.6px;line-height:11px;color:#333}
.contact span{display:inline-block;width:9px;height:8px;margin-left:4px;vertical-align:-1px;background:var(--blue);border-radius:1px}
.contact .web{border-radius:50%}
.contact em{font-style:normal;color:var(--orange)}
.letter{position:absolute;left:50px;top:150px;width:427px;font-size:10.4px;line-height:11.6px}
.letter .recipient{font-weight:700;margin-top:12px}
.letter .address{margin-top:12px}
.letter p.body{margin-top:12px;text-align:justify;hyphens:auto}
.letter .address + p.body{margin-top:28px}
.signature{font-family:"Mrs Saint Delafield",cursive;font-size:26px;margin-top:22px;color:#222}
.letterhead .footer{position:absolute;left:0;right:0;bottom:9px;text-align:center;color:#fff;font-size:10.4px;letter-spacing:.3px}

/* envelope back */
.envelope-back{left:608px;top:19px;width:526px;height:264px}
.envelope-back .wordmark{position:absolute;left:216px;top:46px;font-size:23px;color:#fff}

/* envelope front */
.envelope-front{left:608px;top:294px;width:528px;height:263px}
.envelope-front .wordmark{position:absolute;left:33px;top:64px;font-size:29px}
.return-address{position:absolute;left:33px;top:161px;font-size:10px;line-height:12px;color:#555;letter-spacing:.3px}
.return-address b{font-weight:400;color:var(--blue)}
.envelope-front .url{position:absolute;right:34px;bottom:14px;color:#fff;font-size:9.6px}

/* business cards */
.card-front{left:608px;top:568px;width:234px;height:133px;
  background:radial-gradient(ellipse at 75% 35%,var(--blue-light),var(--blue) 55%,var(--blue-deep))}
.card-front .wordmark{position:absolute;right:28px;top:48px;font-size:25px;color:#fff}
.card-front .url{position:absolute;left:14px;bottom:10px;color:#fff;font-size:7px}
.card-back{left:862px;top:568px;width:234px;height:133px}
.card-back .wordmark{position:absolute;right:20px;top:48px;font-size:21px}
.person{position:absolute;left:18px;top:30px;font-size:7px;line-height:8px}
.person b{color:var(--blue-deep)}
.person .role{color:var(--orange);font-size:5px}
.card-details{position:absolute;left:18px;top:54px;font-size:5px;line-height:6.3px;color:#444}
.card-details b{font-weight:400;color:var(--blue)}
.card-details .lines{margin-top:6px}
.card-details i{display:inline-block;width:5px;height:4px;background:var(--blue-deep);margin-right:3px;vertical-align:0}
</style>
</head>
<body>

<section class="sheet letterhead">
  <div class="wordmark">Solvane Care</div>
  <div class="contact">
    555.014.2290<span></span><br>
    info@solvanecare.com<span></span><br>
    www.<em>Solvane</em>Care.com<span class="web"></span>
  </div>
  <div class="letter">
    <div>Date</div>
    <div class="recipient">Recipient Name</div>
    <div class="address">Company Name<br>Street Address<br>City, State, Zip</div>
    <p class="body">Lorem ipsum dolor sit amet, consectetuer adipiscing elit, sed diam nonummy nibh euismod tincidunt ut laoreet dolore magna aliquam erat volutpat. Ut wisi enim ad minim veniam, quis nostrud exerci tation ullamcorper suscipit lobortis nisl ut aliquip ex ea commodo consequat. Duis autem vel eum iriure dolor in hendrerit in vulputate velit.</p>
    <p class="body">Nam liber tempor cum soluta nobis eleifend option congue nihil imperdiet doming id quod mazim placerat facer possim assum. Typi non habent claritatem insitam; est usus legentis in iis qui facit eorum claritatem. Investigationes demonstraverunt lectores legere me lius quod ii legunt saepius. Claritas est etiam processus dynamicus, qui sequitur mutationem consuetudium lectorum. Mirum est notare quam littera gothica, quam nunc putamus parum claram, anteposuerit litterarum formas humanitatis per seacula quarta.</p>
    <p class="body">Typi non habent claritatem insitam; est usus legentis in iis qui facit eorum claritatem. Investigationes demonstraverunt lectores legere me lius quod ii legunt saepius. Claritas est etiam processus dynamicus, qui sequitur mutationem consuetudium lectorum. Mirum est notare quam littera gothica, quam nunc putamus parum claram, anteposuerit litterarum formas humanitatis per seacula quarta. Typi non habent claritatem insitam; est usus legentis in iis qui facit eorum claritatem. Investigationes demonstraverunt lectores legere me lius quod ii legunt saepius. Claritas est etiam processus dynamicus, qui sequitur mutationem consuetudium lectorum. Mirum est notare quam littera gothica, quam nunc putamus parum claram, anteposuerit litterarum formas humanitatis per seacula quarta.</p>
    <div class="signature">Elin Marsh</div>
  </div>
  <svg class="wave" width="527" height="140" viewBox="0 0 527 140">
    <path d="M0 78 C180 102 380 96 470 62 L527 40 L527 140 L0 140Z" fill="var(--orange)"/>
    <path d="M0 99 C220 109 420 88 527 19 L527 140 L0 140Z" fill="#fff"/>
    <path d="M0 103 C220 112 420 92 527 23 L527 140 L0 140Z" fill="var(--blue)"/>
  </svg>
  <div class="footer">Solvane Care, Suite 123, Street Name, State, Zip 1234, Country</div>
</section>

<section class="sheet envelope-back">
  <svg class="wave" style="top:0;bottom:auto" width="526" height="90" viewBox="0 0 526 90">
    <defs>
      <radialGradient id="flapGlow" cx="0.6" cy="0.2" r="0.6">
        <stop offset="0" stop-color="var(--blue-light)"/>
        <stop offset="1" stop-color="var(--blue)"/>
      </radialGradient>
    </defs>
    <path d="M0 0 H526 L520 25 C505 55 430 60 320 78 C290 84 270 88 250 86 C200 80 140 60 40 48 C15 44 8 30 0 0Z" fill="url(#flapGlow)"/>
  </svg>
  <div class="wordmark">Solvane Care</div>
</section>

<section class="sheet envelope-front">
  <div class="wordmark">Solvane Care</div>
  <div class="return-address">
    <b>Solvane Care</b><br>Suite 123, Street Name<br>State, Zip 1234, Country
  </div>
  <svg class="wave" width="528" height="150" viewBox="0 0 528 150">
    <path d="M0 99 C200 114 380 108 470 78 L528 54 L528 150 L0 150Z" fill="var(--orange)"/>
    <path d="M0 121 C220 129 420 106 528 36 L528 150 L0 150Z" fill="#fff"/>
    <path d="M0 125 C220 133 420 110 528 40 L528 150 L0 150Z" fill="var(--blue)"/>
  </svg>
  <div class="url">www.SolvaneCare.com</div>
</section>

<section class="sheet card-front">
  <div class="wordmark">Solvane Care</div>
  <div class="url">www.SolvaneCare.com</div>
</section>

<section class="sheet card-back">
  <div class="person"><b>Rafe Linden</b><br><span class="role">Managing Director</span></div>
  <div class="card-details">
    <b>Solvane Care</b><br>Suite 123, Street Name<br>State, Zip 1234, Country
    <div class="lines">
      <i></i>555.014.2290<br>
      <i></i>info@solvanecare.com<br>
      <i></i>www.SolvaneCare.com
    </div>
  </div>
  <div class="wordmark">Solvane Care</div>
  <svg class="wave" width="234" height="58" viewBox="0 0 234 58">
    <path d="M0 32 C80 44 170 40 210 27 L234 16 L234 58 L0 58Z" fill="var(--orange)"/>
    <path d="M0 42 C100 48 190 38 234 6 L234 58 L0 58Z" fill="#fff"/>
    <path d="M0 45 C100 51 190 42 234 10 L234 58 L0 58Z" fill="var(--blue)"/>
  </svg>
</section>

</body>
</html>
```